Business Intelligence Application - Reporting Menu and Report Criteria Design

Looking for a fresh, effective and user friendly view for the menu structure and reporting criteria screen format for a business reporting application. Initial format completed, content structure is in place, but we need the 'wow' design.. as its a serious professional report/BI tool it has to fall within certain guidelines for clarity and graphics..but we want it to be slick, friendly, great user experience. There is a large amount of complex content to fit into a small space and we need it to be very inviting, modern and intuitive.. If interested, please review the attachment. We have live screens in operation, but feel these could be improved and looking forward to seeing what great creative suggestions could be made. Please review work done to date in the attached.. We are not looking for a total re-design of everything, all the basic business content/structure is there.. but tell us what we could do to improve this in terms of graphic design... particularly the criteria screens.. thanks!
Updates

Reason: Need a few more days to review designs - thanks for all submissions so far, we will make a selection shortly.

Target Market(s)

Business analysts, hotel operations teams, finance analysts hospitality industry

Industry/Entity Type

Hospitality

Coding

Coded - Design and coding required

Number of Pages Required

4 page

Font styles to use
Sans Serif
Other font styles liked:
• Candara, please see example in deck

Colors
3276b5
3176b5
0255a3
85acd3
33a6d7
cee9f5
85cae6

Requirements
Must have
• sharp clear, logical menu structure, (currently it has 'clicks to sub-menus, we need hover over, slide to sub-menus..) colour, styling.. and most focus on revision of criteria.. right now is somewhat heavy, cumbersome.. keep colour and friendly intuitive process steps.. its heavy analytical stuff.. best of luck!
Should not have
• No grey fonts on white or grey screens! many business apps are not readable or sharp.. or fonts are too small.. colourless, so please avoid that.. see our deck - sharp dark (navy) or black fonts on white, or light shading..

```html
<!DOCTYPE html>
<html lang="en">
<head>
<meta charset="utf-8">
<title>Yield Scope – Property Search</title>
<link rel="stylesheet" href="https://fonts.googleapis.com/css2?family=Mulish:wght@400;600;700;800&family=Open+Sans:wght@400;600&display=swap">
<style>
  :root{
    --navy:#001634;
    --nav-blue:#0255a3;
    --nav-active:#4fb3dc;
    --nav-divider:#5b93cc;
    --stage-top:#33a6d7;
    --stage-bottom:#0b60ae;
    --panel-top:#55b5e0;
    --panel-bottom:#39a1d6;
    --field-top:#ffffff;
    --field-bottom:#ebebeb;
    --field-border:#c4d2dd;
    --field-text:#0f57a6;
    --button:#0255a3;
    --white:#ffffff;
    --accent:#33c4e0;
    --icon:#1f7cc0;
    --footer-bg:#e1e1e1;
    --footer-text:#111111;
  }
  *{box-sizing:border-box;margin:0;padding:0}
  html,body{width:1200px;height:664px;overflow:hidden}
  body{position:relative;font-family:"Mulish",sans-serif;background:var(--stage-bottom)}

  .topbar{position:absolute;left:0;top:0;width:1200px;height:113px;background:var(--navy)}
  .brand{position:absolute;left:97px;top:38px;display:flex;align-items:center;gap:14px}
  .brand-mark{width:36px;height:36px;border-radius:50%;background:var(--accent)}
  .brand-name{font-family:"Open Sans",sans-serif;font-weight:600;font-size:28px;color:var(--white);letter-spacing:-.3px}
  .user{position:absolute;left:781px;top:35px;display:flex;align-items:center;gap:7px}
  .avatar{width:45px;height:45px;border-radius:50%;background:radial-gradient(circle at 50% 40%,#c9b3a3,#6c5a4c)}
  .user-text{font-family:"Open Sans",sans-serif;font-size:14.5px;line-height:19px;color:var(--white)}
  .user-text strong{font-weight:600}
  .divider{position:absolute;top:40px;width:1px;height:38px;background:#1b2c48}
  .bell{position:absolute;left:946px;top:43px}
  .share{position:absolute;left:1036px;top:45px}

  .menu{position:absolute;left:0;top:113px;width:1200px;height:51px;background:var(--nav-blue);display:flex;padding-left:137px}
  .menu-item{height:51px;display:flex;align-items:center;justify-content:center;gap:4px;font-weight:700;font-size:13px;color:var(--white);border-left:1px solid var(--nav-divider);white-space:nowrap}
  .menu-item.active{background:var(--nav-active);border-left-color:var(--nav-active)}
  .menu-badge{width:20px;height:20px;border-radius:50%;background:#d89a55}

  .stage{position:absolute;left:0;top:164px;width:1200px;height:425px;background:linear-gradient(var(--stage-top),var(--stage-bottom))}
  .criteria{position:absolute;left:112px;top:19px;width:974px;height:320px;background:linear-gradient(var(--panel-top),var(--panel-bottom))}
  .field-label{position:absolute;font-weight:700;font-size:16.5px;color:var(--white);letter-spacing:.2px}
  .field-label.plain{font-weight:400;text-transform:none}
  .field{position:absolute;height:43px;background:linear-gradient(var(--field-top),var(--field-bottom));border:1px solid var(--field-border);font-size:15.5px;color:var(--field-text);padding-left:18px;display:flex;align-items:center}
  .field .chevron{position:absolute;right:16px;top:16px}
  .search-button{position:absolute;left:708px;top:233px;width:215px;height:51px;background:var(--button);color:var(--white);font-weight:700;font-size:19.5px;display:flex;align-items:center;justify-content:center;letter-spacing:.3px}

  .footer{position:absolute;left:0;top:589px;width:1200px;height:75px;background:var(--footer-bg);display:flex;align-items:center;justify-content:center;font-family:"Open Sans",sans-serif;font-size:13.5px;color:var(--footer-text);word-spacing:1px}
</style>
</head>
<body>
  <header class="topbar">
    <div class="brand"><span class="brand-mark"></span><span class="brand-name">Yield Scope</span></div>
    <div class="user">
      <div class="avatar" role="img" aria-label="User profile photo"></div>
      <div class="user-text">Welcome<br><strong>Admin</strong></div>
    </div>
    <span class="divider" style="left:919px"></span>
    <svg class="bell" width="28" width-unit="" height="30" viewBox="0 0 28 30" aria-label="Notifications">
      <path d="M14 2c-5.5 0-9 4-9 9v7l-3 4v2h24v-2l-3-4v-7c0-5-3.5-9-9-9z" fill="var(--icon)"/>
      <circle cx="14" cy="27" r="3" fill="var(--icon)"/>
    </svg>
    <span class="divider" style="left:1005px"></span>
    <svg class="share" width="30" height="24" viewBox="0 0 30 24" aria-label="Sign out">
      <path d="M18 2l10 9-10 9v-5.5C10 14.5 5 17 2 22c1-8 6-14 16-15z" fill="var(--icon)"/>
    </svg>
  </header>

  <nav class="menu">
    <a class="menu-item" style="width:100px">Management</a>
    <a class="menu-item" style="width:144px">Rooms Performance</a>
    <a class="menu-item" style="width:134px">Revenue Summary</a>
    <a class="menu-item" style="width:111px">Demand &amp; Risk</a>
    <a class="menu-item" style="width:133px">Inventory Analysis</a>
    <a class="menu-item" style="width:89px">Placeholder</a>
    <a class="menu-item active" style="width:141px"><span class="menu-badge" role="img" aria-label="Mascot icon"></span>Property Search</a>
    <a class="menu-item" style="width:43px">Intel</a>
    <a class="menu-item" style="width:70px">Planning</a>
  </nav>

  <main class="stage">
    <section class="criteria">
      <span class="field-label" style="left:46px;top:43px">SEARCH NAME</span>
      <span class="field-label" style="left:348px;top:43px">SEARCH ID</span>
      <span class="field-label" style="left:641px;top:43px">SEARCH PRODUCT</span>
      <div class="field" style="left:45px;top:73px;width:282px">Pic</div>
      <div class="field" style="left:344px;top:73px;width:282px;font-size:14.5px">876</div>
      <div class="field" style="left:640px;top:73px;width:283px"></div>

      <span class="field-label" style="left:46px;top:145px">DIVISIONS</span>
      <span class="field-label" style="left:348px;top:145px">REGIONS</span>
      <span class="field-label plain" style="left:640px;top:145px">Areas</span>
      <div class="field" style="left:45px;top:175px;width:282px">Europe
        <svg class="chevron" width="24" height="12" viewBox="0 0 24 12"><path d="M1 1l11 10L23 1" fill="none" stroke="#9a9a9a" stroke-width="2"/></svg>
      </div>
      <div class="field" style="left:344px;top:175px;width:282px">UK &amp; Ireland</div>
      <div class="field" style="left:640px;top:175px;width:283px">Central London</div>

      <a class="search-button">SEARCH</a>
    </section>
  </main>

  <footer class="footer">© 2017 Company Name&nbsp; All right reserved&nbsp; Term of Use</footer>
</body>
</html>
```